redesign of my existing custom website into Wordpress based website

I need someone to redesign my current website into something more classy, simplistic, modern and on trend. I would like it set up on Wordpress in a way thats easy for me to make my own additions to blogs/price changes and promotion banners. I will also need a page that is password protected so members can login and have access to all my training videos and resources.
website is www.tidewellmamas.com.au

Target Market(s)

new mums

Industry/Entity Type

Fitness

Coding

Coded - Design and coding required

Number of Pages Required

5+ page

Colors
33a6d7

Requirements
Must have
• chic, modern, stylish and simplistic.
• a call to action above the page fold
• mobile friendly conversion
• a pop up message as soon as someone enters my sight offering my free report
• a members page that is password protected containing 3 youtube videos and 6 pdf attachments as resources
• a home page
• a contact us page
• an about us page
• a blog page
• a store page
Nice to have
• some examples of my peers websites that I like:
• www.norapellwick.com
• https://www.9qlr.com
• https://41bytedgarth.com
Should not have
• anything gimmicky

```html
<!DOCTYPE html>
<html lang="en">
<head>
<meta charset="utf-8">
<title>About Us – Tidewell Mamas</title>
<link href="https://fonts.googleapis.com/css2?family=Lato:wght@400;700&family=Open+Sans:wght@400&display=swap" rel="stylesheet">
<style>
:root{
  --brand:#33a6d7;
  --ink:#222;
  --body:#555;
  --muted:#666;
  --rule:#cfcfcf;
  --band:#e9e9ea;
  --white:#fff;
}
*{box-sizing:border-box;margin:0;padding:0}
html,body{width:834px;height:1200px;overflow:hidden;background:var(--white)}
body{position:relative;font-family:'Open Sans',sans-serif;color:var(--body)}
a{color:inherit;text-decoration:none}
.abs{position:absolute}

.site-header{left:0;top:0;width:834px;height:64px;border-top:2px solid var(--brand);border-bottom:1px solid #d6d6d6;box-shadow:0 1px 3px rgba(0,0,0,.08)}
.brand{display:flex;align-items:center;gap:6px;font-family:'Lato',sans-serif;font-weight:700;color:var(--ink)}
.brand-mark{border:2px solid var(--ink);border-radius:50%}
.header-brand{left:88px;top:16px;font-size:14px}
.header-brand .brand-mark{width:28px;height:28px}
.main-nav{left:238px;top:24px;display:flex;gap:0;font-family:'Lato',sans-serif;font-size:10.5px;color:var(--ink);text-transform:uppercase}
.main-nav a{margin-right:25px}
.main-nav .active{color:var(--brand)}
.btn-login{left:627px;top:19px;width:68px;height:25px;border:1px solid #bbb;border-radius:13px;font-family:'Lato',sans-serif;font-size:10.5px;color:var(--ink);display:flex;align-items:center;justify-content:center;gap:5px}
.btn-join{left:700px;top:20px;width:66px;height:24px;border-radius:12px;background:var(--brand);color:var(--white);font-family:'Lato',sans-serif;font-size:10px;display:flex;align-items:center;justify-content:center}

.breadcrumb{left:68px;top:101px;font-family:'Lato',sans-serif;font-size:10.5px;color:var(--ink)}
.breadcrumb .current{color:var(--brand)}
.breadcrumb-rule{left:68px;top:128px;width:698px;height:1px;background:var(--rule)}

.about-photo{left:68px;top:165px;width:239px;height:298px;border:1px solid #ddd;background:linear-gradient(160deg,#3a3a3a 0%,#d9a58e 30%,#f1c6d6 55%,#8fbf6a 70%,#2e2a2c 100%)}
.about-copy{left:338px;top:161px;width:430px;font-size:8.1px;line-height:17.9px;color:var(--body)}
.about-copy p{margin-bottom:17.9px}

.cta-band{left:0;top:806px;width:834px;height:176px;background:linear-gradient(100deg,#d8d8da 0%,#ececee 35%,#f1e3ea 60%,#e2e2e4 100%);text-align:center}
.cta-band h2{position:absolute;left:0;width:100%;top:36px;font-family:'Lato',sans-serif;font-weight:700;font-size:19.5px;color:#333}
.cta-band p{position:absolute;left:0;width:100%;top:69px;font-family:'Lato',sans-serif;font-size:12.5px;color:#444}
.btn-cta{position:absolute;left:351px;top:104px;width:132px;height:30px;border-radius:15px;background:var(--brand);color:var(--white);font-family:'Lato',sans-serif;font-weight:700;font-size:10.5px;display:flex;align-items:center;justify-content:center}

.footer-brand{left:68px;top:1048px;font-size:19px}
.footer-brand .brand-mark{width:42px;height:42px}
.footer-col h3{font-family:'Open Sans',sans-serif;font-weight:400;font-size:12.5px;color:var(--ink);margin-bottom:9px}
.footer-col{top:1014px;font-size:8.3px;color:var(--muted)}
.quick-links{left:266px}
.quick-links li{list-style:none;line-height:16px}
.subscribe{left:386px;width:200px}
.subscribe p{line-height:16px}
.btn-subscribe{display:flex;margin-top:10px;margin-left:2px;width:83px;height:28px;border-radius:14px;background:var(--brand);color:var(--white);font-family:'Lato',sans-serif;font-size:10px;align-items:center;justify-content:center}
.connected{left:621px}
.social{display:flex;align-items:center;gap:14px;margin-top:3px;margin-bottom:14px}
.social-icon{width:21px;height:21px;border-radius:3px;background:#9a9a9a}
.footer-rule{left:68px;top:1156px;width:698px;height:1px;background:var(--rule)}
.copyright{left:0;top:1173px;width:834px;text-align:center;font-size:8px;color:var(--muted)}
</style>
</head>
<body>

<header class="site-header abs">
  <a class="brand header-brand abs" href="#"><span class="brand-mark"></span>Tidewell Mamas</a>
  <nav class="main-nav abs">
    <a class="active" href="#">Home</a><a href="#">About Us</a><a href="#">Program</a><a href="#">Blog</a><a href="#">FAQ</a><a href="#">Contact Us</a>
  </nav>
  <a class="btn-login abs" href="#">
    <svg width="7" height="9" viewBox="0 0 7 9"><rect x="0" y="4" width="7" height="5" rx="1" fill="#33a6d7"/><path d="M1.5 4V2.6a2 2 0 0 1 4 0V4" stroke="#33a6d7" stroke-width="1.2" fill="none"/></svg>
    LOGIN</a>
  <a class="btn-join abs" href="#">JOIN NOW</a>
</header>

<div class="breadcrumb abs">HOME &nbsp;&gt;&gt;&nbsp; <span class="current">ABOUT US</span></div>
<div class="breadcrumb-rule abs"></div>

<div class="about-photo abs" role="img" aria-label="Photo of the founder smiling and holding her two young daughters"></div>

<article class="about-copy abs">
  <p>After a life time of competitive sports and as a qualified personal trainer, I thought I knew exactly what it would take to get back into shape after having babies. I put on a massive 30 kgs with my first pregnancy and found myself in a situation for the first time in my life where I had to lose a lot of weight. I thought the answer was just to keep training and eating the way I always did before babies, little did I know this wasn't the best way at all. I struggled with losing the weight and I also struggled with a lot of back pain and with abdominal separation that wouldn't fix itself.</p>
  <p>From here i spent a lot of time and energy studying post pregnancy training and found I was doing it all wrong. I totally underestimated the power of core strength and the benefit of easing yourself back into training with the correct post pregnancy specific exercises. I also found my diet was all wrong for someone trying to lose weight with way too much allocation to starchy high GI carbs on my plate and not enough veggies and proteins.</p>
  <p>After my second pregnancy I was so excited to trial out some of my new found knowledge to see how it would go as once again I found myself in a situation of putting on another 25kg. Pleasingly I was able to not only bounce back into shape a lot quicker this time, most importantly I was able to do so without any back pain and my separation also fixed itself within just a few months.</p>
  <p>This is how I came to create the 12 Week Home Workout Program For Mums. I put pen to paper and wrote down all the training routines I used to get back into shape after my second baby. I then tested it out on other mums to make sure it worked for others too and all of the mums I tested on lost at least 18cms across their body doing the program. I also used this exact same program post baby number 3 and at the end of the 12 week program I was fitter and healthier than I had ever been.</p>
  <p>Of course it wasn't just the exercise that helped, it was also a commitment to a healthy eating plan with portion controlled meals that are full of the right mix of protein, vegetables and healthy carbs. The recipes I have put together as part of this program are on constant rotation in my kitchen, so you will see its possible to eat delicious meals and still lose weight at the same time.</p>
  <p>I firmly believe that you do not need to go on any crazy diets, take any pills or spend hours away from the family sweating it out at the gym to get back into shape after you have babies. All it takes is a bit of commitment to regular, post pregnancy specific exercise and a healthy balanced diet. With this combination you will not only be fitter and healthier than ever, you will also have loads more energy for you and your family and be feeling great within yourself!</p>
</article>

<section class="cta-band abs" role="img" aria-label="Faded background photo of a mum resting on a mat after a home workout">
  <h2>It's your turn to take the time to focus on you.</h2>
  <p>Take the first step to being a fitter, healthier more energetic mumma and join my program today!</p>
  <a class="btn-cta" href="#">GET STARTED NOW</a>
</section>

<footer>
  <a class="brand footer-brand abs" href="#"><span class="brand-mark"></span>Tidewell Mamas</a>
  <div class="footer-col quick-links abs">
    <h3>Quick Links</h3>
    <ul><li>Home</li><li>About Us</li><li>Program</li><li>Blog</li><li>Shop</li><li>Contact Us</li></ul>
  </div>
  <div class="footer-col subscribe abs">
    <h3>Subscribe</h3>
    <p>Register your details below and receive tones of free information on fitness and living a healthy lifestyle</p>
    <a class="btn-subscribe" href="#">SUBSCRIBE</a>
  </div>
  <div class="footer-col connected abs">
    <h3>Stay Connected</h3>
    <a class="social" href="#"><span class="social-icon"></span>Friendloop</a>
    <a class="social" href="#"><span class="social-icon"></span>Snapfeed</a>
  </div>
  <div class="footer-rule abs"></div>
  <p class="copyright abs">Copyrights © 2017, Tidewell Mamas. All rights reserved.</p>
</footer>

</body>
</html>
```